Company brochure for our unique consulting business

We are a small consulting business offering a unique set of services to our clients.. In simple terms we are a business improvement consultancy helping our clients get the best out of their businesses. We work with clients across multiple sectors and deliver a variety of services. We want to put together a brochure to cover these main themes:1. Who we are2. What we do3. The type of people we employ4. The sectors we work inWhile the brochure needs to have a certain corporate feel to it, we don't want it to be "boring" or "stiff". We would like it to have a slightly "friendly" or "informal" feel to it, to reflect the type of organisation we are.We have a company website http://brevalconsultingpartners.net , however we do not want to directly replicate the content or feel as we recognise it needs updating.We would like the brochure to be A4 portrait format. We anticipate requiring 12 sides (including covers) but we are happy to be guided on this based on the content we have provided.The attached ppt file gives the detail of the content to be included and also shows the proposed pagination. For the front cover we would like to try 2 versions, one with the BCP logo and one with the Breval Consulting Partners logo (a file of both is attached)One of the most important pages will be the "Our Services" page. We would like this to cover the centre fold. In the ppt file we have shown an example layout, but this is where we need most help - we are clearly not graphic designers! This page will be the most used page in sales meetings etc.Also attached is the following:1. file for our BrevalConsulting Partners company logo.2. File for our BCP company logo3. Files for Derek's signatures (for under photos) - Owen's to follow4. Photo of Derek & Owen (person in purple shirt to be cropped out)Thank you and really excited to see what everyone comes back with.Derek & Owen

Target Market(s)

Very broad - Manufacturing, Healthcare, Hospitality

Industry/Entity Type

Management Consulting

Font styles to use
Other font styles liked:
• We use Swiss721, but happy to be guided by designer

Colors
3276b5
85abd2
0355a3
333333
5c5c5c
9d9d9d
d9d9d9

Requirements
Must have
• Corporate feel
Nice to have
• Slightly friendly feel
• Our standard "blue" is (CORRECTION) - R55 G96 B146 #376092 and our standard grey is R197 G178, B179 - #B3B2B2, which we would like to keep, but other colours we are happy to be guided on. Brand guidelines attached.

```html
<!DOCTYPE html>
<html lang="en">
<head>
<meta charset="utf-8">
<title>Breval Consulting Partners – Brochure Spreads</title>
<link href="https://fonts.googleapis.com/css2?family=Roboto:wght@300;400;500;700&display=swap" rel="stylesheet">
<style>
  :root{
    --brand-blue:#376092;
    --mid-blue:#3276b5;
    --deep-blue:#0355a3;
    --light-blue:#85abd2;
    --ink:#333333;
    --body:#5c5c5c;
    --muted:#9d9d9d;
    --rule:#d9d9d9;
    --stage:#1c1c1c;
    --paper:#ffffff;
  }
  *{box-sizing:border-box;margin:0;padding:0}
  html,body{width:1200px;height:2412px;overflow:hidden;background:var(--stage)}
  body{font-family:"Roboto",Arial,sans-serif;color:var(--ink);position:relative}
  .page{position:absolute;width:552px;height:756px;background:var(--paper);overflow:hidden}
  .col-left{left:32px}.col-right{left:616px}
  .row-1{top:32px}.row-2{top:828px}.row-3{top:1624px}
  .photo{position:absolute}

  /* back cover */
  .back-cover .photo{inset:0;background:linear-gradient(160deg,#f4f6f9 0%,#dfe6ee 35%,#b9cbe0 65%,#e9eef4 100%)}
  .back-cover .shapes{position:absolute;inset:0}
  .address{position:absolute;left:34px;top:588px;font-size:11px;line-height:16px;color:var(--ink);font-weight:500}
  .address .tel{margin-top:6px}
  .back-url{position:absolute;right:40px;bottom:34px;font-size:9px;color:#fff;letter-spacing:.3px}

  /* front cover */
  .cover-title{position:absolute;left:120px;top:30px;font-size:24px;line-height:28px;font-weight:500;color:var(--ink)}
  .cover-title .name{color:var(--brand-blue)}
  .front-cover .photo{left:0;top:90px;width:552px;height:400px;background:linear-gradient(135deg,#dbe4ee 0%,#9fb6cf 45%,#51739b 75%,#2c4a70 100%)}
  .front-cover .shapes{position:absolute;inset:0}
  .wordmark{position:absolute;left:36px;top:590px;display:flex;align-items:center;gap:10px;font-size:30px;font-weight:500;color:var(--brand-blue);line-height:30px}
  .wordmark .dot{width:14px;height:14px;background:var(--brand-blue)}

  /* inner pages */
  .heading{position:absolute;left:36px;top:36px;font-size:26px;font-weight:700;color:var(--ink)}
  .heading.caps{text-transform:uppercase}
  .heading-rule{position:absolute;left:36px;top:78px;width:480px;height:3px;background:var(--brand-blue)}
  .footer-rule{position:absolute;left:36px;right:36px;bottom:34px;height:3px;background:var(--brand-blue)}
  .folio{position:absolute;right:36px;bottom:24px;width:24px;height:22px;background:var(--brand-blue);color:#fff;font-size:10px;font-weight:500;display:flex;align-items:center;justify-content:center}

  .values .photo{left:36px;top:100px;width:480px;height:340px;background:linear-gradient(120deg,#e9eef4 0%,#8fb0d3 45%,#2f5f95 80%,#1d3d66 100%)}
  .values-cols{position:absolute;left:36px;top:470px;width:480px;display:grid;grid-template-columns:1fr 1fr;column-gap:32px}
  .values-cols p{font-size:12px;line-height:17px;color:var(--body);margin-bottom:18px}
  .values-cols b{color:var(--ink);font-weight:700}

  .about .photo{left:36px;top:100px;width:480px;height:320px;background:linear-gradient(180deg,#eef2f6 0%,#c9d6e4 55%,#7e9bbd 100%)}
  .partners{position:absolute;left:36px;top:450px;width:480px;display:grid;grid-template-columns:1fr 1fr;column-gap:40px;text-align:center}
  .partner-name{font-size:22px;font-weight:500;color:var(--ink)}
  .partner-role{font-size:11px;color:var(--muted);margin-top:2px;font-style:italic}
  .partner-bio{font-size:11px;line-height:16px;color:var(--body);margin-top:28px;text-align:center}

  .regions .map{position:absolute;left:36px;top:150px;width:480px;height:330px;background:linear-gradient(135deg,#e6eef7 0%,#c5d7ea 50%,#9fbcdb 100%)}
  .region-pin{position:absolute;display:flex;align-items:center;gap:6px}
  .region-pin .tag{background:#fff;border:1px solid var(--brand-blue);color:var(--ink);font-size:10px;font-weight:500;padding:3px 7px;white-space:nowrap}

  .people-copy{position:absolute;left:36px;top:100px;width:480px}
  .people-copy p{font-size:12px;line-height:17px;color:var(--body);margin-bottom:15px}
  .people .photo{left:36px;top:410px;width:480px;height:290px;background:linear-gradient(135deg,#f3f5f8 0%,#d3dce6 50%,#9aaec4 100%)}
</style>
</head>
<body>

<section class="page col-left row-1 back-cover">
  <div class="photo" role="img" aria-label="Photograph of a hand pressing glowing digital interface buttons in pale blue tones"></div>
  <svg class="shapes" width="552" height="756" viewBox="0 0 552 756">
    <polygon points="200,756 330,560 460,560 330,756" fill="#376092"/>
    <polygon points="290,756 420,580 552,580 552,756" fill="#0355a3"/>
    <polygon points="150,756 230,640 270,640 190,756" fill="#85abd2" opacity=".8"/>
  </svg>
  <div class="address">
    Harcourt House<br>Mill Lane<br>Leeds<br>LS2 7QP<br>United Kingdom
    <div class="tel">Tel: +44 (0)113 496 0215</div>
  </div>
  <div class="back-url">www.brevalconsultingpartners.net</div>
</section>

<section class="page col-right row-1 front-cover">
  <h1 class="cover-title">business improvement by<br><span class="name">breval consulting partners</span></h1>
  <div class="photo" role="img" aria-label="Photograph of two businessmen in suits reviewing documents at a desk"></div>
  <svg class="shapes" width="552" height="756" viewBox="0 0 552 756">
    <polygon points="0,90 90,90 0,230" fill="#fff"/>
    <polygon points="0,300 70,420 0,490" fill="#376092"/>
    <polygon points="0,490 60,400 130,490" fill="#0355a3"/>
    <polygon points="0,490 552,490 552,470 330,470" fill="#fff"/>
    <polygon points="380,756 470,620 552,620 552,756" fill="#376092"/>
    <polygon points="470,756 552,650 552,756" fill="#0355a3"/>
  </svg>
  <div class="wordmark"><span class="dot"></span>breval consulting partners</div>
</section>

<section class="page col-left row-2 values">
  <h2 class="heading caps">Our Values</h2>
  <div class="heading-rule"></div>
  <div class="photo" role="img" aria-label="Photograph of a hand touching a grid of illuminated blue squares"></div>
  <div class="values-cols">
    <div>
      <p>Be <b>TRUSTED</b> by our team and clients, so that our opinions are sought and our recommendations valued.</p>
      <p>Have a tight-knit relationship with our clients, so we are seen as a <b>PARTNER</b> and not just supplier.</p>
      <p>Be focused on return on investment, but professionally, always deliver <b>GREAT VALUE.</b></p>
    </div>
    <div>
      <p><b>DEVELOP &amp; GROW</b> all our team people to continually help one step ahead.</p>
      <p>Work relentlessly to deliver results for our clients. And ensure we collectively <b>ENJOY THE JOURNEY.</b></p>
      <p>Take <b>SOCIAL RESPONSIBILITY</b> seriously by supporting other worthwhile organisations.</p>
    </div>
  </div>
  <div class="footer-rule"></div>
  <div class="folio">03</div>
</section>

<section class="page col-right row-2 about">
  <h2 class="heading">About Us</h2>
  <div class="heading-rule"></div>
  <div class="photo" role="img" aria-label="Photograph of the two partners seated side by side in an office"></div>
  <div class="partners">
    <div>
      <div class="partner-name">Owen Hartley</div>
      <div class="partner-role">Partner</div>
      <p class="partner-bio">At BCP our community values sit behind everything we do for our clients. Owen leads our operations practice and brings twenty years of hands-on improvement experience.</p>
    </div>
    <div>
      <div class="partner-name">Derek Whitcombe</div>
      <div class="partner-role">Partner</div>
      <p class="partner-bio">We bring together our expertise from many sectors and a wide range of consulting roles, helping organisations to achieve more with individual goals.</p>
    </div>
  </div>
  <div class="footer-rule"></div>
  <div class="folio">04</div>
</section>

<section class="page col-left row-3 regions">
  <h2 class="heading">Our Regions</h2>
  <div class="heading-rule"></div>
  <div class="map" role="img" aria-label="World map in blue marking the regions where the firm works"></div>
  <div class="region-pin" style="left:70px;top:200px">
    <span class="tag">North America</span>
    <svg width="12" height="16" viewBox="0 0 12 16"><path d="M6 0a6 6 0 0 0-6 6c0 4.5 6 10 6 10s6-5.5 6-10a6 6 0 0 0-6-6z" fill="#376092"/><circle cx="6" cy="6" r="2.2" fill="#fff"/></svg>
  </div>
  <div class="region-pin" style="left:250px;top:180px">
    <svg width="12" height="16" viewBox="0 0 12 16"><path d="M6 0a6 6 0 0 0-6 6c0 4.5 6 10 6 10s6-5.5 6-10a6 6 0 0 0-6-6z" fill="#376092"/><circle cx="6" cy="6" r="2.2" fill="#fff"/></svg>
    <span class="tag">UK &amp; Europe</span>
  </div>
  <div class="region-pin" style="left:300px;top:280px">
    <svg width="12" height="16" viewBox="0 0 12 16"><path d="M6 0a6 6 0 0 0-6 6c0 4.5 6 10 6 10s6-5.5 6-10a6 6 0 0 0-6-6z" fill="#376092"/><circle cx="6" cy="6" r="2.2" fill="#fff"/></svg>
    <span class="tag">Middle East</span>
  </div>
  <div class="region-pin" style="left:380px;top:360px">
    <svg width="12" height="16" viewBox="0 0 12 16"><path d="M6 0a6 6 0 0 0-6 6c0 4.5 6 10 6 10s6-5.5 6-10a6 6 0 0 0-6-6z" fill="#376092"/><circle cx="6" cy="6" r="2.2" fill="#fff"/></svg>
    <span class="tag">Asia Pacific</span>
  </div>
  <div class="footer-rule"></div>
  <div class="folio">05</div>
</section>

<section class="page col-right row-3 people">
  <h2 class="heading">Our People</h2>
  <div class="heading-rule"></div>
  <div class="people-copy">
    <p>All of our team at BCP started their careers in operational roles. This means we understand what it is like to be in your shoes. Blending this understanding with our years of experience and skills we are able to work in partnership with you and your teams to deliver great results.</p>
    <p>We also recognise no single person knows everything, so within the team we have experts in their own fields. They are able to bring their specialist skills and experience at the right time and to the best effect.</p>
    <p>Our team also understand the importance of engagement. Everyone in your team will get to know us as the same faces, because we take the time to listen to everyone, from shop floor to senior management.</p>
  </div>
  <div class="photo" role="img" aria-label="Photograph of hands over a desk with printed charts, a laptop and a pen"></div>
  <div class="footer-rule"></div>
  <div class="folio">06</div>
</section>

</body>
</html>
```